Parcelwise HQ letterhead and envelope

Design a formal (8.5x11) letterhead and envelope for sales outreach and legal matters. Using design input from https://www.parcelwisehq.example/ and the attached documents.

Industry/Entity Type

Software Service

Requirements
Must have
• These 4 hex colors are our official colors:
• #355c98 [blue]
• #1eb1a2 [teal]
• #fdba12 [gold]
• #f1653b [orange]
• So no other colors besides these should be used.

```html
<!DOCTYPE html>
<html lang="en">
<head>
<meta charset="utf-8">
<title>Parcelwise HQ Letterhead</title>
<link href="https://fonts.googleapis.com/css2?family=Lato:wght@400;700&family=Arimo:wght@400&family=Kaushan+Script&display=swap" rel="stylesheet">
<style>
  :root {
    --brand-blue: #355c98;
    --text-grey: #555555;
    --text-dark: #222222;
    --backdrop: #e9e9e9;
    --paper: #ffffff;
    --paper-shade: #f3f3f3;
    --faint-blue: #dfe5ee;
  }
  * { margin: 0; padding: 0; box-sizing: border-box; }
  html, body {
    width: 996px; height: 1200px; overflow: hidden;
    background: var(--backdrop);
  }
  .letterhead {
    position: absolute; left: 76px; top: 20px;
    width: 844px; height: 1160px; overflow: hidden;
    background: linear-gradient(135deg, var(--paper) 40%, var(--paper-shade) 100%);
    font-family: "Lato", sans-serif;
  }
  .header-band { position: absolute; left: 0; top: 36px; }
  .contact-lines {
    position: absolute; left: 69px; top: 43px;
    font-family: "Arimo", sans-serif; font-size: 13.5px; color: #ffffff;
    line-height: 24px;
  }
  .contact-lines .item { display: inline-flex; align-items: center; gap: 5px; margin-right: 8px; }
  .contact-lines svg { width: 13px; height: 13px; }
  .brand {
    position: absolute; left: 520px; top: 40px;
    display: flex; align-items: center; gap: 12px;
  }
  .brand-dot {
    width: 50px; height: 50px; border-radius: 50%;
    border: 4px solid var(--brand-blue);
  }
  .brand-name {
    font-family: "Lato", sans-serif; font-weight: 400;
    font-size: 38px; color: var(--brand-blue); letter-spacing: 0.5px;
  }
  .letter-body { position: absolute; left: 72px; top: 256px; width: 700px; }
  .salutation { font-weight: 700; font-size: 16px; color: var(--brand-blue); margin-bottom: 20px; }
  .paragraph {
    font-size: 16px; line-height: 26.2px; color: var(--text-grey);
    margin-bottom: 20px; text-align: justify;
  }
  .closing { font-size: 19px; color: var(--text-dark); margin-top: 34px; }
  .signature {
    font-family: "Kaushan Script", cursive; font-size: 32px;
    color: var(--brand-blue); margin-top: 4px;
  }
  .faint-ring {
    position: absolute; left: 568px; top: 860px;
    width: 290px; height: 290px; border-radius: 50%;
    border: 14px solid var(--faint-blue);
  }
  .address {
    position: absolute; left: 72px; top: 1122px;
    display: flex; align-items: center; gap: 5px;
    font-family: "Arimo", sans-serif; font-size: 13.5px; color: var(--text-dark);
  }
  .address svg { width: 12px; height: 13px; }
</style>
</head>
<body>
<main class="letterhead">
  <svg class="header-band" width="540" height="58" viewBox="0 0 540 58" aria-hidden="true">
    <path d="M0 0 H532 C506 16 506 42 532 58 H0 Z" fill="var(--brand-blue)"/>
  </svg>
  <div class="contact-lines">
    <div>
      <span class="item"><svg viewBox="0 0 14 14"><circle cx="7" cy="7" r="6" fill="none" stroke="#fff" stroke-width="1.3"/><rect x="4.5" y="3.5" width="5" height="7" rx="1" fill="none" stroke="#fff" stroke-width="1"/></svg>(555) 014-2288</span>
      <span class="item"><svg viewBox="0 0 14 14"><circle cx="7" cy="7" r="6" fill="none" stroke="#fff" stroke-width="1.3"/><path d="M4.5 4 Q4 8 8 10 L9.5 8.8 L8.3 7.6 L7.5 8.2 Q6 7.3 5.8 5.8 L6.4 5 L5.3 3.8 Z" fill="#fff"/></svg>(555) 010-4400(Main)</span>
    </div>
    <div>
      <span class="item"><svg viewBox="0 0 14 14"><circle cx="7" cy="7" r="6" fill="none" stroke="#fff" stroke-width="1.2"/><ellipse cx="7" cy="7" rx="2.6" ry="6" fill="none" stroke="#fff" stroke-width="1"/><path d="M1 7 H13" stroke="#fff" stroke-width="1"/></svg>www.parcelwisehq.example</span>
      <span class="item"><svg viewBox="0 0 14 14"><circle cx="7" cy="7" r="6" fill="none" stroke="#fff" stroke-width="1.3"/><circle cx="7" cy="7" r="2.2" fill="none" stroke="#fff" stroke-width="1.2"/></svg>jsmith@parcelwisehq.example</span>
    </div>
  </div>
  <div class="brand">
    <span class="brand-dot" aria-hidden="true"></span>
    <span class="brand-name">Parcelwise HQ</span>
  </div>

  <section class="letter-body">
    <p class="salutation">Dear Mr. Lorem,</p>
    <p class="paragraph">Lorem ipsum dolor sit amet, consectetuer adipiscing elit, sed diam nonummy nibh euismod tincidunt ut laoreet dolore magna aliquam erat volutpat. Ut wisi enim ad minim veniam, quis nostrud exerci tation ullamcorper suscipit lobortis nisl ut aliquip ex ea commodo consequat. Duis autem vel eum iriure dolor in hendiusto odio dignissim qui blandit praesent luptatum zzril delenit augue duis dolore te feugait nulla facilisi.</p>
    <p class="paragraph">Lorem ipsum dolor sit amet, consectetuer adipiscing elit, sed diam nonummy nibh euismod tincidunt ut laoreet dolore magna aliquam erat volutpat. Ut wisi enim ad minim veniam, quis nostrud exerci tation ullamcorper suscipit lobortis nisl ut aliquip ex ea commodo consequat. Duis autem vel eum iriure dolor in hendiusto odio dignissim qui blandit praesent luptatum zzril delenit augue duis dolore te feugait nulla facilisi.</p>
    <p class="paragraph">Lorem ipsum dolor sit amet, consectetuer adipiscing elit, sed diam nonummy nibh euismod tincidunt ut laoreet dolore magna aliquam erat volutpat. Ut wisi enim ad minim veniam, quis nostrud exerci tation ullamcorper suscipit lobortis nisl ut aliquip ex ea commodo consequat. Duis autem vel eum iriure dolor in hendiusto odio dignissim qui blandit praesent luptatum zzril delenit augue duis dolore te feugait nulla facilisi.</p>
    <p class="closing">Sincerely Your,</p>
    <p class="signature">Your Name</p>
  </section>

  <div class="faint-ring" aria-hidden="true"></div>

  <div class="address">
    <svg viewBox="0 0 12 13"><circle cx="6" cy="6.5" r="5.5" fill="none" stroke="var(--brand-blue)" stroke-width="1.2"/><path d="M6 3.2 A2 2 0 0 1 8 5.2 C8 6.8 6 9.5 6 9.5 C6 9.5 4 6.8 4 5.2 A2 2 0 0 1 6 3.2 Z" fill="var(--brand-blue)"/></svg>
    27 Lantern Row, Fairview, OR 97000
  </div>
</main>
</body>
</html>
```